Marwick Law Letterhead

We need a new letterhead design for a Law Firm. The address for the law firm is 1475 Calloway Street, Suite 210, Houston, Texas 77041. Phone Number: 832-361-9027; Fax Number: 832-614-7359. The logo is uploaded to the project.

```html
<!DOCTYPE html>
<html lang="en">
<head>
<meta charset="utf-8">
<title>Marwick Law Letterhead</title>
<link href="https://fonts.googleapis.com/css2?family=Roboto:wght@400;500&display=swap" rel="stylesheet">
<style>
  :root {
    --navy: #14264f;
    --red: #c81e2a;
    --ink: #333333;
    --paper: #f4f4f4;
    --backdrop: #e2e2e2;
    --sig-fill: #e6e6e6;
  }
  * { margin: 0; padding: 0; box-sizing: border-box; }
  html, body {
    width: 1069px; height: 1200px; overflow: hidden;
    background: var(--backdrop);
    font-family: "Roboto", Arial, sans-serif;
    color: var(--ink);
  }
  .letterhead {
    position: absolute; left: 119px; top: 13px;
    width: 830px; height: 1174px;
    background: var(--paper);
    box-shadow: 0 4px 18px rgba(0,0,0,0.12);
    overflow: hidden;
  }
  .brand {
    position: absolute; left: 50px; top: 88px;
    display: flex; align-items: center; gap: 12px;
  }
  .brand-mark { width: 34px; height: 34px; background: var(--navy); }
  .brand-name {
    font-weight: 500; font-size: 38px; letter-spacing: 0.5px;
    color: var(--navy); line-height: 1;
  }
  .contact {
    position: absolute; left: 598px; top: 52px;
    font-size: 16.5px; line-height: 20.5px; color: #222;
  }
  .contact-line { display: flex; align-items: center; gap: 6px; margin-top: 5px; }
  .contact-line + .contact-line { margin-top: 4px; }
  .contact-line svg { width: 14px; height: 14px; fill: var(--red); }
  .header-rule {
    position: absolute; left: 50px; width: 732px;
  }
  .header-rule.red { top: 193px; height: 2px; background: var(--red); }
  .header-rule.navy { top: 197px; height: 4px; background: var(--navy); }
  .recipient {
    position: absolute; left: 50px; top: 333px;
    font-size: 15px; line-height: 23.6px;
  }
  .body-text {
    position: absolute; left: 50px; width: 732px; top: 445px;
    font-size: 15px; line-height: 23.6px; text-align: justify;
  }
  .body-text p + p { margin-top: 21px; }
  .body-text p.gap-lg { margin-top: 26px; }
  .closing {
    position: absolute; left: 50px; top: 839px; font-size: 15px;
  }
  .signature {
    position: absolute; left: 50px; top: 880px;
    width: 150px; height: 56px; background: var(--sig-fill); border-radius: 3px;
  }
  .footer-band { position: absolute; left: 0; bottom: 0; width: 830px; height: 26px; }
</style>
</head>
<body>
<main class="letterhead">
  <div class="brand">
    <span class="brand-mark"></span>
    <span class="brand-name">Marwick Law</span>
  </div>

  <address class="contact" style="font-style:normal">
    <div>1475 Calloway Street,</div>
    <div>Suite 210, Houston,</div>
    <div>Texas 77041</div>
    <div class="contact-line">
      <svg viewBox="0 0 24 24" aria-hidden="true"><path d="M6.6 10.8a15.1 15.1 0 0 0 6.6 6.6l2.2-2.2a1 1 0 0 1 1-.25 11.4 11.4 0 0 0 3.6.57 1 1 0 0 1 1 1V20a1 1 0 0 1-1 1A17 17 0 0 1 3 4a1 1 0 0 1 1-1h3.5a1 1 0 0 1 1 1c0 1.25.2 2.45.57 3.57a1 1 0 0 1-.25 1z"/></svg>
      <span>832-361-9027</span>
    </div>
    <div class="contact-line">
      <svg viewBox="0 0 24 24" aria-hidden="true"><path d="M6 2h12v5H6zM4 8h16a2 2 0 0 1 2 2v7h-4v5H6v-5H2v-7a2 2 0 0 1 2-2zm4 8v4h8v-4z"/></svg>
      <span>832-614-7359</span>
    </div>
  </address>

  <div class="header-rule red"></div>
  <div class="header-rule navy"></div>

  <div class="recipient">
    <div>Mr/s</div>
    <div>First Name and Last Name</div>
    <div>Company Name</div>
    <div>Address</div>
  </div>

  <section class="body-text">
    <p>Lorem Ipsum is simply dummy text of the printing and typesetting industry. Lorem Ipsum has been the industry's standard dummy text ever since the 1500s, when an unknown printer took a galley of type and scrambled it to make a type specimen book. It has survived not only five centuries, but also the leap into electronic typesetting, remaining essentially unchanged. It was popularised in the 1960s with the release of Typeline sheets containing Lorem Ipsum passages.</p>
    <p class="gap-lg">he standard chunk of Lorem Ipsum used since the 1500s is reproduced below for those interested. Sections 1.10.32 and 1.10.33 from "de Finibus Bonorum et Malorum" by Aurelian are also reproduced in their exact original form, accompanied by English versions from the 1914 translation by J. Whitcombe. Lorem ipsum dolor sit amet, consectetur adipiscing elit, sed do eiusmod tempor incididunt ut labore et dolore magna aliqua.</p>
    <p>It is a long established fact that a reader will be distracted by the readable content of a page when looking at its layout. The point of using Lorem Ipsum is that it has a more-or-less normal distribution of letters, as opposed to using 'Content here, content here', making it look like readable English. Many desktop publishing packages and web page editors now .</p>
  </section>

  <div class="closing">Your Sincerely,</div>
  <div class="signature" role="img" aria-label="Handwritten signature"></div>

  <svg class="footer-band" viewBox="0 0 830 26" preserveAspectRatio="none" aria-hidden="true">
    <defs>
      <linearGradient id="navyBand" x1="0" x2="1">
        <stop offset="0" stop-color="#13224a"/>
        <stop offset="1" stop-color="#1c3263"/>
      </linearGradient>
      <linearGradient id="redBand" x1="0" x2="1">
        <stop offset="0" stop-color="#d4212b"/>
        <stop offset="1" stop-color="#7e1117"/>
      </linearGradient>
    </defs>
    <polygon points="0,0 596,0 567,26 0,26" fill="url(#navyBand)"/>
    <polygon points="612,0 830,0 830,26 583,26" fill="url(#redBand)"/>
  </svg>
</main>
</body>
</html>
```